The Harlow Reserve Web Site design

I need a web design for my luxury range of Terry Toweling and Spa Accessories for luxury upmarket hotels and Spas. I have a catalog that sets the mood and tone I am looking for. I need a website design that shows off the look and feel of this luxury range while working back to the catalog look and feel. Its all about Upmarket and Luxury. I will be using the website as a reference site and as a site that customers can purchase off.
The Logo is attached as is the catalog. I don't mind changing the color of the Logo to match the website. However I would prefer to keep the font of that logo.

http://thegallerydesk.pixvault-example.com/p504729381
Please can you try and access this link. The Harlow Reserve
Name Greta. Email greta@vellumsupply-example.com.au. Password Harlow.
These images are to be used for shopping page and please use the close up details of texture as background on pages and use those texture details and close ups for banners

Please note the look and feel has to be very upmarket and super luxury. Ficus is on mood and not on retail.
Have a look at the mood on the following websites
Www.gracefulretreats-example.com
And yourcosyseasidecabin-example.com
That one is retail .mi don't want retail focus but it's very clean. And simple and colors are good
Updates

Please rebook brief. I have added some important detail. Thanks

Relook brief. I have added,important detail. Thanks

Target Market(s)

Corporate buyers
This is not for retail selling to consumers
Price it's viewed only after secure login

Industry/Entity Type

Shopping

Colors
acd037
cadf82
fbc995
fce7d3
faa54b

Requirements
Must have
• Luxury. Think luxury. Very high end yet modern like the catalogue
Use banners on home page
Should not have
• Don't use the blue as the main color. It's too cheap.
No products on home page

```html
<!DOCTYPE html>
<html lang="en">
<head>
<meta charset="utf-8">
<title>The Harlow Reserve</title>
<link href="https://fonts.googleapis.com/css2?family=Lobster&family=Libre+Baskerville&family=Arimo:wght@400;700&family=Open+Sans:ital,wght@0,600;1,600&display=swap" rel="stylesheet">
<style>
:root{
  --orange:#faa54b;
  --orange-deep:#f39a32;
  --green:#acd037;
  --green-soft:#cadf82;
  --peach:#fbc995;
  --cream:#fce7d3;
  --ink:#222;
  --text:#555;
  --muted:#777;
  --band:#f2f2f2;
  --line:#bdbdbd;
  --white:#fff;
}
*{box-sizing:border-box;margin:0;padding:0}
html,body{width:1034px;height:1200px;overflow:hidden}
body{position:relative;background:var(--white);font-family:'Arimo',Arial,sans-serif;color:var(--ink)}
.abs{position:absolute}
a{color:inherit;text-decoration:none}

/* header */
.cart-icon{left:765px;top:4px;width:23px;height:23px;border-radius:50%;background:var(--green)}
.account-links{left:809px;top:7px;font-size:13px;display:flex;gap:14px}
.logo{left:137px;top:32px;font-family:'Lobster',cursive;font-size:38px;color:var(--orange);line-height:1}
.search{left:594px;top:43px;width:139px;height:26px;border:1px solid #ccc;font-size:11px;font-style:italic;color:#444;padding:5px 6px}
.search svg{position:absolute;right:5px;top:4px}
.call{left:763px;top:40px;width:134px}
.call svg{position:absolute;left:0;top:3px}
.call-label{text-align:right;font-size:12px}
.call-number{text-align:right;font-size:17px;margin-top:0}

.main-nav{left:137px;top:90px;width:759px;height:42px;border-top:1px dotted #999;border-bottom:1px dotted #999}
.main-nav a{position:absolute;top:10px;font-family:'Libre Baskerville',serif;font-size:14px;color:#333}
.main-nav a.active{color:var(--orange)}
.main-nav a.active::after{content:"";position:absolute;left:-1px;right:-1px;bottom:-7px;height:2px;background:var(--green)}

/* hero */
.hero{left:137px;top:153px;width:760px;height:304px;overflow:hidden;
  background:linear-gradient(180deg,#8a8580 0%,#6e6a66 35%,#a89584 65%,#7a6656 100%)}
.hero-caption{position:absolute;left:0;right:0;top:232px;text-align:center;color:var(--white);
  font-family:'Libre Baskerville',serif;font-size:22px;line-height:27px}
.hero-arrow{position:absolute;top:137px;width:30px;height:30px;border-radius:50%;background:var(--white)}
.hero-arrow.prev{left:-15px}
.hero-arrow.next{right:-15px}
.hero-arrow svg{position:absolute;top:9px}
.hero-arrow.prev svg{left:17px}
.hero-arrow.next svg{left:8px}

/* categories */
.categories{left:0;top:468px;width:1034px;height:290px;background:var(--band)}
.category{position:absolute;top:19px;width:165px}
.category-photo{width:161px;height:133px}
.category h3{font-family:'Lobster',cursive;font-weight:400;font-size:22px;color:#555;margin-top:12px;margin-left:-4px}
.category p{font-size:12.5px;line-height:15px;color:var(--text);margin-top:4px;margin-left:-4px}
.btn{display:inline-block;background:var(--green);color:var(--white);font-family:'Open Sans',sans-serif;font-weight:600;font-size:11.5px;height:19px;line-height:19px;padding:0 7px}
.category .btn{position:absolute;top:234px;left:-4px}
.divider{position:absolute;top:20px;height:252px;border-left:1px dotted var(--line)}

/* about + brochure */
.section-title{font-size:17px;color:var(--orange-deep);font-weight:400}
.about{left:144px;top:789px;width:545px}
.about p{font-size:11.3px;line-height:16px;margin-top:12px;color:var(--ink)}
.about .btn{margin-top:10px;margin-left:0}
.brochure{left:721px;top:789px;width:180px}
.brochure p{font-size:11.3px;line-height:16px;margin-top:12px;margin-left:2px}
.pdf-btn{position:absolute;left:2px;top:88px;width:174px;height:30px;border-radius:3px;
  background:linear-gradient(180deg,var(--green-soft),var(--green));color:var(--white);
  font-family:'Arimo',sans-serif;font-weight:700;font-size:15px;line-height:30px;padding-left:45px}
.pdf-btn svg{position:absolute;left:0;top:-4px}

/* clients */
.clients{left:0;top:934px;width:1034px;height:98px;background:var(--band)}
.clients-title{position:absolute;left:153px;top:39px;font-family:'Open Sans',sans-serif;font-style:italic;font-weight:600;font-size:16px;color:var(--orange-deep)}
.client{position:absolute;top:40px;font-family:'Libre Baskerville',serif;font-size:15px;color:#777;display:flex;align-items:center;gap:7px}
.client i{display:inline-block;width:9px;height:9px;border-radius:50%;background:#999}

/* footer */
.footer{left:0;top:1032px;width:1034px;height:145px;background:#fafafa}
.footer h4{font-size:12.5px;font-weight:700;color:var(--ink)}
.footer-col{position:absolute;top:16px}
.footer-col ul{list-style:none;margin-top:7px}
.footer-col li{font-size:10.5px;line-height:13.8px}
.newsletter p{font-size:10.5px;line-height:14px;margin-top:7px}
.email-field{margin-top:20px;width:121px;height:19px;border:1px solid #888;background:var(--white);font-size:10px;font-style:italic;color:#666;padding:3px 6px}
.newsletter .btn{margin-top:12px;width:62px;text-align:center;font-size:11.5px}
.contact dl{margin-top:7px}
.contact-row{display:flex;font-size:10.5px;line-height:14px;margin-bottom:9px}
.contact-row dt{width:15px;font-size:12px}
.social{display:flex;gap:4px;margin-top:7px}
.social span{width:21px;height:21px;border-radius:50%;background:#2b2b2b}
.payment-badge{margin-top:7px;margin-left:12px;width:106px;height:67px;background:var(--white);border:1px solid #e3e3e3;padding:8px 10px}
.payment-badge span{display:inline-block;width:17px;height:10px;margin-right:2px;border-radius:1px}

.bottom-bar{left:0;top:1177px;width:1034px;height:23px;background:var(--orange)}
.copyright{position:absolute;left:153px;top:5px;font-size:10.5px;color:#333}
.bottom-logo{position:absolute;left:749px;top:1px;font-family:'Lobster',cursive;font-size:15px;color:#333}
</style>
</head>
<body>

<header>
  <span class="abs cart-icon" aria-hidden="true">
    <svg width="23" height="23" viewBox="0 0 23 23"><path d="M6 7h2l1.5 6h6l1.5-4.5H9" fill="none" stroke="#fff" stroke-width="1.6"/><circle cx="10" cy="16" r="1.2" fill="#fff"/><circle cx="15" cy="16" r="1.2" fill="#fff"/></svg>
  </span>
  <nav class="abs account-links"><a href="#">Login</a><a href="#">Register</a></nav>
  <div class="abs logo">The Harlow Reserve</div>
  <div class="abs search">Search here
    <svg width="16" height="16" viewBox="0 0 16 16"><circle cx="6.5" cy="6.5" r="4.5" fill="none" stroke="#acd037" stroke-width="2.2"/><path d="M10 10l4.5 4.5" stroke="#acd037" stroke-width="2.6" stroke-linecap="round"/></svg>
  </div>
  <div class="abs call">
    <svg width="24" height="24" viewBox="0 0 24 24"><circle cx="12" cy="12" r="11" fill="none" stroke="#faa54b" stroke-width="1.5"/><path d="M8 6c-1.5 1-1.5 3 0 6s3.5 5 5.5 6c1.5.6 2.5 0 3-1l-2-2-1.5 1c-1.5-.8-3-2.5-3.8-4l1-1.5-2-2.5z" fill="#faa54b"/></svg>
    <div class="call-label">Call Us Today</div>
    <div class="call-number">123-456-7890</div>
  </div>
  <nav class="abs main-nav">
    <a class="active" href="#" style="left:8px">Home</a>
    <a href="#" style="left:111px">About Us</a>
    <a href="#" style="left:232px">Products</a>
    <a href="#" style="left:351px">New Collection</a>
    <a href="#" style="left:509px">Accessories</a>
    <a href="#" style="left:644px">Contact Us</a>
  </nav>
</header>

<section class="abs hero" role="img" aria-label="Spa room with a freestanding white bathtub and massage beds draped in soft terry throws">
  <p class="hero-caption">We Allows You To Transform Your Bathroom, Spa, or<br>Poolside Into A True Retreat.</p>
  <span class="hero-arrow prev"><svg width="7" height="12" viewBox="0 0 7 12"><path d="M6 1L1 6l5 5" fill="none" stroke="#222" stroke-width="1.8"/></svg></span>
  <span class="hero-arrow next"><svg width="7" height="12" viewBox="0 0 7 12"><path d="M1 1l5 5-5 5" fill="none" stroke="#222" stroke-width="1.8"/></svg></span>
</section>

<section class="abs categories">
  <article class="category" style="left:149px">
    <div class="category-photo" role="img" aria-label="Poolside massage table dressed in white towels beside palm trees" style="background:linear-gradient(180deg,#3a4a3c 0%,#29352c 45%,#8f969a 75%,#c9c5bd 100%)"></div>
    <h3>Spa Accessories</h3>
    <p>Lorem ipsum dolor sit amet consectetuer adipiscing elit sed diam nonu euismod</p>
    <a class="btn" href="#">Read More</a>
  </article>
  <span class="divider" style="left:326px"></span>
  <article class="category" style="left:339px">
    <div class="category-photo" role="img" aria-label="Stack of red, navy and orange terry towels" style="background:linear-gradient(180deg,#e8403a 0%,#d63a34 30%,#2b3642 55%,#f07a28 75%,#f25a1e 100%)"></div>
    <h3>Terry Towels</h3>
    <p>Lorem ipsum dolor sit amet consectetuer adipiscing elit sed diam nonummy nibh euismod</p>
    <a class="btn" href="#">Read More</a>
  </article>
  <span class="divider" style="left:516px"></span>
  <article class="category" style="left:531px">
    <div class="category-photo" role="img" aria-label="Folded woven throws in green, navy and charcoal" style="background:linear-gradient(160deg,#4b5a3c 0%,#2f3550 40%,#3a3a48 70%,#5e5650 100%)"></div>
    <h3>Throws</h3>
    <p>Lorem ipsum dolor sit amet consectetuer adipiscing elit sed diam nonummy nibh euismod</p>
    <a class="btn" href="#">Read More</a>
  </article>
  <span class="divider" style="left:706px"></span>
  <article class="category" style="left:725px">
    <div class="category-photo" role="img" aria-label="Striped blankets in turquoise, red and grey hanging on a hook" style="background:linear-gradient(135deg,#b8bcbe 0%,#7cc6cf 30%,#e8e4de 50%,#c8403c 68%,#9a9a9a 100%)"></div>
    <h3>New Collection</h3>
    <p>Lorem ipsum dolor sit amet consectetuer adipiscing elit sed diam nonummy nibh euismod</p>
    <a class="btn" href="#">Read More</a>
  </article>
</section>

<section class="abs about">
  <h2 class="section-title">About Us</h2>
  <p>Lorem ipsum dolor sit amet, consectetuer adipiscing elit, sed diam nonummy nreibh euismod tincidunt ut laoreet dolore magna aliquam erat volutpat. Ut wisi enim ad min veniam, quis nostrud exerci tation ullam. Lorem ipsum dolor sit amet, consectetuer adipiscing elit, sed diam nonummy nreibh euismod tincidunt ut laoreet dolore magna aliquam erat volutpat. Ut wisi enim ad min veniam, quis nostrud exerci tation ullam</p>
  <a class="btn" href="#">Read More</a>
</section>

<section class="abs brochure">
  <h2 class="section-title">Download Our Brochure</h2>
  <p>Lorem ipsum dolor sit amet, consec Lorem ipsum dolor sit amet, consec readipiscing elit sed diam non</p>
  <a class="pdf-btn" href="#">
    <svg width="30" height="38" viewBox="0 0 30 38"><path d="M2 2h19l7 7v27H2z" fill="#fff" stroke="#cadf82" stroke-width="1.5"/><path d="M21 2v7h7" fill="none" stroke="#cadf82" stroke-width="1.5"/><rect x="2" y="6" width="17" height="8" fill="#acd037"/><path d="M6 30c6-4 10-10 12-16" stroke="#acd037" stroke-width="1.5" fill="none"/></svg>
    Download PDF
  </a>
</section>

<section class="abs clients">
  <h2 class="clients-title">Some of&nbsp; Our Clients</h2>
  <span class="client" style="left:343px">The Calloway</span>
  <span class="client" style="left:484px">Marisol Bay</span>
  <span class="client" style="left:623px">Evenfall Hotels</span>
  <span class="client" style="left:762px"><i></i>The Aldenmoor</span>
</section>

<footer class="abs footer">
  <div class="footer-col" style="left:154px">
    <h4>Quick Links</h4>
    <ul><li>Home</li><li>About Us</li><li>Products</li><li>New Collection</li><li>Accessories</li><li>Contact Us</li></ul>
  </div>
  <div class="footer-col" style="left:261px">
    <h4>Service &amp; Support</h4>
    <ul><li>My Account</li><li>Terms &amp; Conditions</li><li>Buying Guide</li><li>Shipping Details</li><li>FAQ's</li><li>My Cart</li><li>Terms of Use</li></ul>
  </div>
  <div class="footer-col newsletter" style="left:391px">
    <h4>Newsletter SignUp</h4>
    <p>Join Our newsletter list<br>to get the latest updates</p>
    <div class="email-field">email address</div>
    <a class="btn" href="#">Submit</a>
  </div>
  <div class="footer-col contact" style="left:546px">
    <h4>Contact Information</h4>
    <dl>
      <div class="contact-row"><dt>A:</dt><dd>Street Name, City Name<br>State Zip Code</dd></div>
      <div class="contact-row"><dt>P:</dt><dd>123-456-7890</dd></div>
      <div class="contact-row"><dt>F:</dt><dd>456-789-4504</dd></div>
      <div class="contact-row"><dt>E:</dt><dd>Support@harlowreserve-example.com</dd></div>
    </dl>
  </div>
  <div class="footer-col" style="left:755px">
    <h4>Follow Us On</h4>
    <div class="social" aria-label="Social links"><span></span><span></span><span></span><span></span><span></span></div>
    <div class="payment-badge" aria-label="Accepted payment methods">
      <span style="background:#d9a441"></span><span style="background:#8d8fb8"></span><span style="background:#7aa7c7"></span><span style="background:#e9a24a"></span>
      <div style="height:12px"></div>
      <span style="background:#b9b9b9"></span><span style="background:#d9a441"></span><span style="background:#7aa7c7"></span><span style="background:#e9a24a"></span>
    </div>
  </div>
</footer>

<div class="abs bottom-bar">
  <span class="copyright">©2014&nbsp; TheHarlowReserve&nbsp; All Rights Reserved</span>
  <span class="bottom-logo">The Harlow Reserve</span>
</div>

</body>
</html>
```